Business Card - Tidal Lanes

Need Business Card design for company named Tidal Lanes. Software development focused mainly on Brindle Orvix & Zelt Apps. I've attached our logo with both a black and white background. Please add trademark symbol to logo when using.

```html
<!DOCTYPE html>
<html lang="en">
<head>
<meta charset="utf-8">
<title>Tidal Lanes – Business Card</title>
<link href="https://fonts.googleapis.com/css2?family=Open+Sans:wght@400;600;700&display=swap" rel="stylesheet">
<style>
  :root {
    --stage: #e6e3de;
    --paper: #ffffff;
    --ink: #1d1d1d;
    --accent-red: #d91e2a;
    --accent-orange: #ee7d1c;
    --accent-yellow: #f7be14;
    --ghost: #e4e4e6;
    --night: #0b0b0b;
    --night-soft: #2a2a2a;
  }
  html, body {
    margin: 0;
    width: 1200px;
    height: 1014px;
    overflow: hidden;
    background: var(--stage);
    font-family: "Open Sans", Arial, sans-serif;
  }
  .canvas {
    position: relative;
    width: 1200px;
    height: 1014px;
  }
  .card {
    position: absolute;
    left: 250px;
    width: 700px;
    height: 400px;
    box-shadow: 0 10px 28px rgba(0,0,0,0.22);
    overflow: hidden;
  }
  /* Front */
  .card--front {
    top: 60px;
    background: var(--paper);
  }
  .front__dot {
    position: absolute;
    left: -34px;
    top: 40px;
    width: 68px;
    height: 68px;
    border-radius: 50%;
    background: var(--accent-red);
  }
  .front__wordmark {
    position: absolute;
    right: 48px;
    top: 60px;
    margin: 0;
    font-size: 64px;
    font-weight: 700;
    color: var(--ghost);
    letter-spacing: -1px;
  }
  .front__identity {
    position: absolute;
    left: 60px;
    top: 40px;
  }
  .front__name {
    margin: 0;
    font-size: 27px;
    font-weight: 700;
    color: var(--ink);
    line-height: 1.15;
  }
  .front__role {
    margin: 0;
    font-size: 23px;
    color: var(--accent-red);
    line-height: 1.2;
  }
  .front__contact {
    position: absolute;
    left: 60px;
    top: 150px;
    font-size: 19px;
    line-height: 1.35;
    color: var(--ink);
  }
  .front__contact p { margin: 0; }
  .front__web { color: var(--accent-red); }
  .front__address { margin-top: 16px !important; }
  .front__bands {
    position: absolute;
    left: 0;
    bottom: 0;
    width: 100%;
    height: 24px;
    display: flex;
  }
  .band { height: 100%; }
  .band--yellow { flex: 0 0 36%; background: var(--accent-yellow); }
  .band--orange { flex: 0 0 32%; background: var(--accent-orange); }
  .band--red { flex: 1; background: var(--accent-red); }

  /* Back */
  .card--back {
    top: 540px;
    background: linear-gradient(160deg, var(--night) 0%, var(--night) 55%, var(--night-soft) 100%);
    display: flex;
    align-items: center;
    justify-content: center;
  }
  .back__brand {
    display: flex;
    align-items: center;
    gap: 18px;
  }
  .back__mark {
    width: 26px;
    height: 26px;
    border-radius: 50%;
    background: var(--accent-orange);
  }
  .back__name {
    margin: 0;
    font-size: 40px;
    font-weight: 600;
    color: #ffffff;
    letter-spacing: -0.5px;
  }
</style>
</head>
<body>
<main class="canvas">
  <section class="card card--front" aria-label="Business card front">
    <div class="front__dot"></div>
    <p class="front__wordmark">Tidal Lanes</p>
    <div class="front__identity">
      <h1 class="front__name">Dana Whitfield</h1>
      <p class="front__role">Manager</p>
    </div>
    <div class="front__contact">
      <p>555-204-6318 Mobile</p>
      <p>555-730-4472 Fax</p>
      <p>dana@tidallanes.com</p>
      <p class="front__web">tidallanes.com</p>
      <p class="front__address">4120 Harbor Row</p>
      <p>Easton, FL 34010</p>
    </div>
    <div class="front__bands">
      <div class="band band--yellow"></div>
      <div class="band band--orange"></div>
      <div class="band band--red"></div>
    </div>
  </section>

  <section class="card card--back" aria-label="Business card back">
    <div class="back__brand">
      <span class="back__mark"></span>
      <p class="back__name">Tidal Lanes™</p>
    </div>
  </section>
</main>
</body>
</html>
```